New Bicycle shop business card

Hi!
I'm looking for a business card for my new proffesional bike mechanics shop. This shop is only for fixing broken bikes and not selling bikes.
Peferbly a modern and sleek and modern design.
Colors: black, grey, red, white
Information:
Name: Rijwielwerkplaats Vanhoutte
Shop owner: Bart Vanhoutte & Marieke Segers
Website: www.rijwielwerkplaats-vanhoutte.be
Email: info@rijwielwerkplaats-vanhoutte.be
Phone number: +32471902368
Street adres: Kerkweg 46
9940 Bellebeke
Slogan/shop information: Herstellingen van alle merken.
Logo: see files.
Target Market(s)
People who seek a mechanic to fix or upgrade their bikes.
Contact Information for Business Card
Information:
Website: info@rijwielwerkplaats-vanhoutte.be
9940 Bellebeke
Logo: see files.

```html
<!DOCTYPE html>
<html lang="nl">
<head>
<meta charset="utf-8">
<title>Rijwielwerkplaats Vanhoutte – Business Card</title>
<link rel="stylesheet" href="https://fonts.googleapis.com/css2?family=Open+Sans:wght@400;600;700&display=swap">
<style>
  :root {
    --stage: #3a3b3d;
    --card-white: #ffffff;
    --card-black: #060606;
    --brand-red: #e8202e;
    --ink: #1b1b1b;
    --grey: #9a9a9a;
    --grey-dark: #8a8a8a;
  }
  * { margin: 0; padding: 0; box-sizing: border-box; }
  html, body {
    width: 1200px; height: 900px; overflow: hidden;
    background: var(--stage);
    font-family: "Open Sans", Arial, sans-serif;
  }
  .canvas {
    position: relative; width: 1200px; height: 900px;
    display: flex; flex-direction: column; align-items: center; justify-content: center; gap: 36px;
  }
  .card {
    position: relative; width: 700px; height: 400px;
    border-radius: 30px; overflow: hidden;
    box-shadow: 0 14px 30px rgba(0,0,0,.45);
  }

  /* Back side */
  .card--back { background: var(--card-black); }
  .back-mark {
    position: absolute; left: 400px; top: 120px;
    display: flex; align-items: center; gap: 12px;
  }
  .back-mark__dot { width: 22px; height: 22px; border-radius: 50%; background: var(--brand-red); }
  .back-mark__name { color: var(--card-white); font-weight: 700; font-size: 22px; line-height: 1.15; }
  .slogan {
    position: absolute; left: 0; right: 0; bottom: 92px;
    text-align: center; color: var(--card-white); font-size: 15px; font-weight: 600;
  }

  /* Front side */
  .card--front { background: var(--card-white); }
  .front-accent { position: absolute; inset: 0; width: 100%; height: 100%; }
  .top-tab { position: absolute; top: 0; right: 0; width: 26px; height: 34px; background: var(--brand-red); }
  .owners { position: absolute; top: 26px; right: 40px; text-align: right; }
  .owners__label { color: var(--brand-red); font-size: 17px; font-weight: 600; }
  .owners__names { color: var(--grey-dark); font-size: 20px; font-weight: 700; }

  .wordmark {
    position: absolute; left: 56px; top: 110px;
    display: flex; align-items: center; gap: 12px;
  }
  .wordmark__dot { width: 24px; height: 24px; border-radius: 50%; background: var(--brand-red); }
  .wordmark__name { color: var(--ink); font-weight: 700; font-size: 20px; line-height: 1.15; }

  .contact { position: absolute; left: 56px; top: 184px; }
  .contact__company { color: var(--brand-red); font-size: 21px; font-weight: 700; }
  .contact__role { color: var(--ink); font-size: 15px; font-weight: 600; margin-bottom: 8px; }
  .contact__address { color: var(--grey); font-size: 15px; line-height: 1.35; margin-bottom: 6px; }
  .contact__list { list-style: none; }
  .contact__item { display: flex; align-items: center; gap: 10px; color: var(--grey); font-size: 15px; line-height: 1.6; }
  .contact__icon { width: 14px; height: 14px; flex: none; }

  .front-mark {
    position: absolute; right: 34px; bottom: 34px;
    color: var(--card-white); font-weight: 700; font-size: 17px; line-height: 1.2; text-align: right;
  }
</style>
</head>
<body>
<main class="canvas">

  <section class="card card--back" aria-label="Achterkant visitekaartje">
    <div class="back-mark">
      <span class="back-mark__dot"></span>
      <span class="back-mark__name">Rijwielwerkplaats<br>Vanhoutte</span>
    </div>
    <p class="slogan">Herstellingen van alle merken.</p>
  </section>

  <section class="card card--front" aria-label="Voorkant visitekaartje">
    <svg class="front-accent" viewBox="0 0 700 400" preserveAspectRatio="none" aria-hidden="true">
      <path d="M700,100 Q560,290 380,400 L700,400 Z" fill="#e8202e"/>
    </svg>
    <span class="top-tab"></span>

    <div class="owners">
      <p class="owners__label">Shop owner:</p>
      <p class="owners__names">Bart Vanhoutte &amp; Marieke Segers</p>
    </div>

    <div class="wordmark">
      <span class="wordmark__dot"></span>
      <span class="wordmark__name">Rijwielwerkplaats<br>Vanhoutte</span>
    </div>

    <div class="contact">
      <p class="contact__company">Rijwielwerkplaats Vanhoutte</p>
      <p class="contact__role">General Manager</p>
      <p class="contact__address">Kerkweg 46<br>9940 Bellebeke</p>
      <ul class="contact__list">
        <li class="contact__item">
          <svg class="contact__icon" viewBox="0 0 24 24" aria-hidden="true"><path fill="#e8202e" d="M6.6 10.8a15 15 0 0 0 6.6 6.6l2.2-2.2a1 1 0 0 1 1-.25 11.4 11.4 0 0 0 3.6.57 1 1 0 0 1 1 1V20a1 1 0 0 1-1 1A17 17 0 0 1 3 4a1 1 0 0 1 1-1h3.5a1 1 0 0 1 1 1c0 1.25.2 2.45.57 3.57a1 1 0 0 1-.25 1z"/></svg>
          +32471902368
        </li>
        <li class="contact__item">
          <svg class="contact__icon" viewBox="0 0 24 24" aria-hidden="true"><rect x="2" y="5" width="20" height="14" rx="2" fill="#e8202e"/><path d="M3 6l9 7 9-7" fill="none" stroke="#fff" stroke-width="2"/></svg>
          info@rijwielwerkplaats-vanhoutte.be
        </li>
        <li class="contact__item">
          <svg class="contact__icon" viewBox="0 0 24 24" aria-hidden="true"><circle cx="12" cy="12" r="10" fill="#e8202e"/><path d="M2 12h20M12 2c3 3 3 17 0 20M12 2c-3 3-3 17 0 20" fill="none" stroke="#fff" stroke-width="1.5"/></svg>
          www.rijwielwerkplaats-vanhoutte.be
        </li>
      </ul>
    </div>

    <p class="front-mark">Rijwielwerkplaats<br>Vanhoutte</p>
  </section>

</main>
</body>
</html>
```